Brightwell Aero Services Logo

I need a website and logo for the parent company Brightwell Aero Services, which encompasses general aviation aircraft repair, small aircrat rental and flight school. The company is based in Lawrenceville, Georgia at the Tolleson county airport. A saying that can be incorporated somehere could be, "Quality flying is safe flying", "Safety in mind is no accident" ,. I need a website and logo.

The company started as a repair shop performing repairs and inspections on Harlan, Vantor, Delkin and Ralstead general aviation aircraft, all models of single engine piston, multi engine piston, and single engine turboprop with an emphasis on Harlan Solvane and AeroTurn turbo prop aircraft. We have se=ince entered the aircraft rental and flight instruction market using the Delkin 240 ang Harlan Ranger aircraft.

Number of Pages; I don't know. Maybe 5 ? A home page for Brightwell Aero Services, page for maintenance and repairs and a couple for the rental and school. The maintenance shop is busy, always has been. I need to get the rental and school advertised and busy.

I have a logo for the maintenance shop shirts, not for the school. I do not have the file. I paid a business locally to do that and print on the shirts. They have the file.

Target Market(s)

In our flight school rental fleet department, we are looking for persons wishing to obtain their private pilot license and continuing on into their commercial and instrument ratings. In the aircraft maintenance department, we are looking for new customers who want a better and more quality relationship with their aircraft maintenance provider who will give more detail and quality in the repairs with an emphasis on safety and fewer problems between scheduled maintenance cycles on their aircraft. Brightwell's owner, Dale Hutchins, has been performing aircraft maintenance in the Atlanta area for 27 years. He has built a steady customer base through those years.

```html
<!DOCTYPE html>
<html lang="en">
<head>
<meta charset="UTF-8">
<title>Brightwell Aero Services</title>
<link href="https://fonts.googleapis.com/css2?family=Poppins:wght@600;700;800&family=Lato:wght@400;700;900&display=swap" rel="stylesheet">
<style>
:root{
  --blue:#1f8fd6;
  --blue-deep:#2f5aa8;
  --blue-light:#a9d4f0;
  --ink:#222426;
  --text:#555;
  --white:#fff;
  --mist:#f5f6f8;
}
*{margin:0;padding:0;box-sizing:border-box}
html,body{width:1200px;height:3215px;overflow:hidden;background:var(--white)}
body{position:relative;font-family:'Lato',sans-serif;color:var(--text)}
.abs{position:absolute}
.btn{position:absolute;display:flex;align-items:center;justify-content:center;background:linear-gradient(90deg,#2496d9,#2a6fbf);color:var(--white);font-family:'Poppins',sans-serif;font-weight:700;font-size:14px;letter-spacing:.2px}

/* header */
.social{top:47px;left:111px;display:flex;gap:4px}
.social span{width:40px;height:40px;border-radius:50%;background:var(--blue);display:block}
.brand{top:8px;left:0;width:1200px;text-align:center;font-family:'Poppins',sans-serif;font-weight:800;color:var(--blue);font-size:30px;line-height:34px;letter-spacing:1px}
.brand small{display:block;font-size:15px;line-height:20px;letter-spacing:2px}
.search{top:47px;left:904px;width:40px;height:40px;border-radius:50%;background:var(--blue-deep)}
.login{top:42px;left:974px;width:114px;height:50px;border:2px solid var(--blue);color:var(--blue-deep);font-family:'Poppins',sans-serif;font-weight:700;font-size:15px;display:flex;align-items:center;justify-content:center}
.rule{top:141px;left:111px;width:977px;height:3px;background:var(--blue-deep)}
.nav{top:166px;left:0;width:1200px;height:24px;font-size:15px;color:#333}
.nav a{position:absolute;transform:translateX(-50%);text-decoration:none;color:inherit}

/* hero */
.hero{top:212px;left:0;width:1200px;height:648px;background:linear-gradient(100deg,#2a2c2e 0%,#4a4c4c 40%,#6f6a63 70%,#55575a 100%)}
.hero-frame{top:328px;left:111px;width:535px;height:311px;border:4px solid var(--white);border-bottom:none}
.hero-frame::before,.hero-frame::after{content:"";position:absolute;bottom:0;height:4px;background:var(--white)}
.hero-frame::before{left:-4px;width:174px}
.hero-frame::after{right:-4px;width:166px}
.hero-title{top:400px;left:111px;width:535px;text-align:center;font-family:'Poppins',sans-serif;font-weight:800;font-size:52px;line-height:77px;color:var(--white)}
.hero-title em{font-style:normal;color:var(--blue)}
.hero-cta{top:612px;left:301px;width:155px;height:51px}
.arrow{width:50px;height:50px;border-radius:50%}
.arrow.prev{top:501px;left:51px;background:var(--blue)}
.arrow.next{top:499px;left:1088px;background:var(--white)}

/* about */
.about-photo{top:921px;left:137px;width:457px;height:340px;background:linear-gradient(160deg,#5d6a6a,#9a9c98 55%,#6d6b66)}
.about-head{top:900px;left:672px;font-family:'Poppins',sans-serif;font-weight:800;font-size:34px;color:var(--blue)}
.about-copy{top:980px;left:672px;width:420px;font-size:15px;line-height:25.7px}
.about-cta{top:1203px;left:672px;width:155px;height:50px}

/* services */
.services{top:1364px;left:0;width:1200px;height:643px;background:linear-gradient(120deg,#d9dadb,#eceded 45%,#dcdcdc 80%,#cfd0d1)}
.services-head{top:1455px;left:0;width:1200px;text-align:center;font-family:'Poppins',sans-serif;font-weight:800;font-size:34px;color:var(--blue)}
.card{position:absolute;top:1548px;width:302px;height:356px}
.card-img{position:absolute;inset:0}
.card.one .card-img{clip-path:polygon(0 17px,100% 0,100% 323px,0 100%);background:linear-gradient(160deg,#7d8385,#4a4f56 60%,#3c4250)}
.card.two .card-img{clip-path:polygon(0 0,100% 0,100% 323px,0 323px);background:linear-gradient(180deg,#d8624f 0%,#7e8a93 12%,#6b7560 55%,#8a7d68 100%)}
.card.three .card-img{clip-path:polygon(0 0,100% 17px,100% 100%,0 323px);background:linear-gradient(160deg,#a9acaf,#3b3b3d 55%,#2f3136)}
.card-label{position:absolute;top:258px;left:0;width:100%;text-align:center;font-family:'Poppins',sans-serif;font-weight:700;font-size:21px;color:var(--white)}
.plus{position:absolute;left:131px;width:40px;height:34px;background:var(--blue)}
.plus::before,.plus::after{content:"";position:absolute;background:var(--white);left:50%;top:50%;transform:translate(-50%,-50%)}
.plus::before{width:14px;height:4px}
.plus::after{width:4px;height:14px}

/* rental */
.rental-box{top:2134px;left:509px;width:484px;height:297px;border:2px solid var(--blue-deep)}
.rental-photo{top:2093px;left:190px;width:394px;height:288px;background:linear-gradient(170deg,#8f979c,#c9cdd0 45%,#7d8388 80%,#b4b8bb)}
.rental-head{top:2153px;left:628px;font-family:'Poppins',sans-serif;font-weight:800;font-size:32px;line-height:40px;color:var(--blue)}
.rental-copy{top:2250px;left:628px;width:336px;font-size:12px;line-height:21.5px}
.rental-cta{top:2359px;left:628px;width:139px;height:45px;font-size:13px}

/* footer */
.footer-bg{top:2516px;left:0;width:1200px;height:400px;background:var(--mist)}
.foot-h{font-family:'Poppins',sans-serif;font-weight:700;font-size:25px;color:var(--ink);top:2674px}
.foot-line{top:2716px;width:42px;height:3px;background:var(--blue)}
.foot-p{top:2740px;font-size:15px;line-height:22px;width:300px}
.call-small{top:2797px;left:160px;font-size:12px;color:var(--ink)}
.call-num{top:2810px;left:160px;font-family:'Lato',sans-serif;font-weight:900;font-size:22px;color:var(--blue-deep)}
.email{top:2791px;left:440px;width:360px;height:46px;border:1px solid #bbb;border-radius:23px;background:var(--white)}
.email span{position:absolute;left:18px;top:14px;font-size:14px;color:#777}
.subscribe{top:2796px;left:666px;width:129px;height:36px;border-radius:18px;background:var(--blue);color:var(--white);font-family:'Poppins',sans-serif;font-weight:700;font-size:15px;display:flex;align-items:center;justify-content:center}
.follow{top:2737px;left:867px;display:flex;gap:6px}
.follow span{width:37px;height:37px;border-radius:50%;border:2px solid var(--blue);display:block}
.links{top:2791px;left:870px;font-size:15px;line-height:22.5px;color:var(--ink)}

.partners{top:2916px;left:0;width:1200px;height:299px;background:var(--blue-deep)}
.partner{position:absolute;top:38px;width:163px;height:125px;background:var(--white);display:flex;align-items:center;justify-content:center;font-family:'Poppins',sans-serif;font-weight:700;font-size:24px;color:var(--ink)}
.partner-rule{top:216px;left:111px;width:977px;height:1px;background:rgba(255,255,255,.35)}
.copyright{top:246px;left:0;width:1200px;text-align:center;font-size:14px;color:var(--white)}
</style>
</head>
<body>

<header>
  <div class="abs social" aria-label="Social links"><span></span><span></span><span></span><span></span></div>
  <div class="abs brand">BRIGHTWELL<small>AERO SERVICES</small></div>
  <div class="abs search" aria-label="Search">
    <svg width="40" height="40" viewBox="0 0 40 40"><circle cx="19" cy="19" r="5" fill="none" stroke="#fff" stroke-width="2"/><line x1="22.5" y1="22.5" x2="26" y2="26" stroke="#fff" stroke-width="2"/></svg>
  </div>
  <div class="abs login">LOG IN</div>
  <div class="abs rule"></div>
  <nav class="abs nav">
    <a style="left:333px">HOME</a>
    <a style="left:457px">ABOUT US</a>
    <a style="left:593px">SERVICES</a>
    <a style="left:710px">BLOG</a>
    <a style="left:841px">CONTACT US</a>
  </nav>
</header>

<section>
  <div class="abs hero" role="img" aria-label="Aircraft parked inside a maintenance hangar"></div>
  <svg class="abs" style="top:700px;left:0" width="1200" height="160" viewBox="0 0 1200 160">
    <defs><linearGradient id="band" x1="0" x2="1"><stop offset="0" stop-color="#1f95d8"/><stop offset="1" stop-color="#2f5aa8"/></linearGradient></defs>
    <polygon points="0,134 899,4 1200,130 1200,160 0,160" fill="url(#band)"/>
    <polygon points="0,160 899,26 1200,160" fill="#fff"/>
  </svg>
  <div class="abs hero-frame"></div>
  <h1 class="abs hero-title">QUALITY <em>FLYING</em> IS<br>SAFE FLYING</h1>
  <div class="btn hero-cta">GET STARTED</div>
  <div class="abs arrow prev"><svg width="50" height="50" viewBox="0 0 50 50"><polyline points="28,16 19,25 28,34" fill="none" stroke="#fff" stroke-width="3"/></svg></div>
  <div class="abs arrow next"><svg width="50" height="50" viewBox="0 0 50 50"><polyline points="22,16 31,25 22,34" fill="none" stroke="#2f5aa8" stroke-width="3"/></svg></div>
</section>

<section>
  <svg class="abs" style="top:907px;left:124px" width="485" height="371" viewBox="0 0 485 371" fill="none" stroke="#2f8fd6" stroke-width="3">
    <polyline points="96,2 2,2 2,96"/><polyline points="389,2 483,2 483,96"/>
    <polyline points="2,275 2,369 96,369"/><polyline points="483,275 483,369 389,369"/>
  </svg>
  <div class="abs about-photo" role="img" aria-label="Hangar floor with several light aircraft under repair"></div>
  <h2 class="abs about-head">ABOUT US</h2>
  <p class="abs about-copy">Lorem ipsum dolor sit amet, consectetur adipiscing elit, sed do eiusmod tempor incididunt ut labore et dolore magna aliqu Ut enim ad minim veniam, quis nostrud exercitation ullam laboris nisi ut aliquip ex ea commodo consequat. Duis aute irure dolor in reprehenderit in voluptate velit esse cillum dolore eu fugiat nulla pariatur. Excepteur sint occaecat cupidatat non proident, sunt in culpa qui officia deserunt mollit anim id est laborum.</p>
  <div class="btn about-cta">LEARN MORE</div>
</section>

<section>
  <div class="abs services" role="img" aria-label="Faded background of a mechanic at work"></div>
  <h2 class="abs services-head">OUR SERVICES</h2>
  <div class="card one" style="left:111px">
    <div class="card-img" role="img" aria-label="Technician servicing a jet engine"></div>
    <div class="card-label">Aircraft Repair</div>
    <div class="plus" style="top:315px"></div>
  </div>
  <div class="card two" style="left:450px">
    <div class="card-img" role="img" aria-label="Small ultralight aircraft on an airfield"></div>
    <div class="card-label">Small Aircraft Rental</div>
    <div class="plus" style="top:306px"></div>
  </div>
  <div class="card three" style="left:787px">
    <div class="card-img" role="img" aria-label="Instructor and student reviewing a flight plan beside an aircraft"></div>
    <div class="card-label">Flight school</div>
    <div class="plus" style="top:315px"></div>
  </div>
</section>

<section>
  <div class="abs rental-box"></div>
  <svg class="abs" style="top:2118px;left:941px" width="70" height="68" viewBox="0 0 70 68"><polygon points="0,0 69,0 69,67" fill="#8cc8ee"/></svg>
  <div class="abs rental-photo" role="img" aria-label="Passenger jet parked in a bright hangar"></div>
  <h2 class="abs rental-head">RENTAL AND<br>SCHOOL</h2>
  <p class="abs rental-copy">Lorem ipsum dolor sit amet, consectetur adipiscing elit, sed do eiusmod tempor incididunt ut labore et dolore magna cillum dolore eu fugiat nulla pariatur. Excepteur sint deserunt mollit anim id est laborum.</p>
  <div class="btn rental-cta">LEARN MORE</div>
</section>

<footer>
  <div class="abs footer-bg"></div>
  <svg class="abs" style="top:2516px;left:0" width="1200" height="130" viewBox="0 0 1200 130">
    <polygon points="0,0 1200,0 1200,52 0,0" fill="#fff"/>
    <polygon points="740,56 1200,52 1200,118" fill="#cfe4f5"/>
    <polygon points="830,62 1200,68 1200,120" fill="#a9c8ea"/>
  </svg>

  <h3 class="abs foot-h" style="left:111px">Brightwell Aero</h3>
  <div class="abs foot-line" style="left:111px"></div>
  <p class="abs foot-p" style="left:114px">Lorem ipsum dolor sit amet, consectetur adipiscing</p>
  <svg class="abs" style="top:2798px;left:111px" width="34" height="34" viewBox="0 0 34 34" fill="none" stroke="#2f5aa8" stroke-width="2"><path d="M7 4 L12 4 L14 11 L10 14 Q13 21 20 24 L23 20 L30 22 L30 27 Q29 31 24 30 Q8 26 4 10 Q3 5 7 4Z"/><path d="M20 6 Q27 7 28 14"/><path d="M20 10 Q24 11 24 14"/></svg>
  <div class="abs call-small">Call us</div>
  <div class="abs call-num">+1 (888) 888 8888</div>

  <h3 class="abs foot-h" style="left:438px">Subscribe to Newsletter</h3>
  <div class="abs foot-line" style="left:438px"></div>
  <p class="abs foot-p" style="left:441px">Lorem ipsum dolor sit amet, consectetur adipiscing</p>
  <div class="abs email"><span>Email*</span></div>
  <div class="abs subscribe">Subscribe</div>

  <h3 class="abs foot-h" style="left:867px">Follow Us</h3>
  <div class="abs foot-line" style="left:867px"></div>
  <div class="abs follow" aria-label="Social links"><span></span><span></span><span></span><span></span><span></span></div>
  <div class="abs links">Sitemap<br>Privacy Policy<br>Website Accessibility Policy</div>

  <div class="abs partners">
    <div class="partner" style="left:207px">Harlan</div>
    <div class="partner" style="left:415px">Vantorcraft</div>
    <div class="partner" style="left:622px">Delkin</div>
    <div class="partner" style="left:829px">Ralstead</div>
    <div class="abs partner-rule"></div>
    <div class="abs copyright">©Copyrights 2023 Company Name &nbsp;|&nbsp; All Rights Reserved</div>
  </div>
</footer>

</body>
</html>
```